EB-5 Regional Center needs a Web design

Harlow Ridge Financial Partners is an expanding EB-r regional center. We have been successful in sponsoring multiple projects of third-party developers and placing EB-5, B-1, and Private Investments into multiple projects.

We are now partnering directly with project developers in the energy and healthcare to raise foreign capital for projects in those industries. The foreign capital is used as project equity and our collective balance sheets are used to guarantee debt to complete the funding of the projects.

We need a web site where we can post our company credentials, the bios of each partner, a document page for each of our projects where we can post specific project related documents which foreign investors can read, and we will need a section where foreign investors can fill out investor forms confirming that they are qualified investors and leaving their contact so that our agents and executives can make contact.

The final design should reflect the exceptional experience of the partners and our financial strength and stability.

We do have a logo we would want to use on the web design.

Target Market(s)

EB-5 Investors, B-1 Investors, Private Equity and other investors seeking quality investment in job creating US projects.

Coding

Number of Pages Required

5+ page

Font styles to use
Sans Serif

Requirements
Must have
• Pages to display company info, partner bios, projects completed, and a projects in-process page where we can post documents and info on projects for which we are seeking foreign investment. We also need a section where investors can enter their qualifying personal information and leave contact information for us.

```html
<!DOCTYPE html>
<html lang="en">
<head>
<meta charset="utf-8">
<title>Harlow Ridge Financial Partners</title>
<link href="https://fonts.googleapis.com/css2?family=Lato:wght@400;700;900&display=swap" rel="stylesheet">
<style>
:root{
  --ink:#1e1e1e;
  --text:#444;
  --muted:#666;
  --grey-btn:#7d7d7d;
  --band:#f3f3f3;
  --wave:#d6d6d6;
  --wave-light:#e6e6e6;
  --line:#dcdcdc;
  --dark:#2a2a2a;
  --white:#fff;
}
*{box-sizing:border-box;margin:0;padding:0}
html,body{width:1200px;height:4839px;overflow:hidden}
body{position:relative;background:var(--white);font-family:'Lato',sans-serif;color:var(--text)}
.abs{position:absolute}
.center{text-align:center}

/* header */
.site-header{top:0;left:0;width:1200px;height:122px;background:var(--white)}
.brand{left:76px;top:36px;display:flex;align-items:center;gap:14px}
.brand-mark{width:40px;height:40px;background:#8a8a8a}
.brand-name{font-size:22px;font-weight:700;color:#6d6d6d;line-height:1.1;width:220px}
.main-nav{right:72px;top:42px;display:flex;gap:6px}
.main-nav a{font-size:14px;font-weight:700;color:var(--ink);text-decoration:none;padding:12px 17px}
.main-nav a.active{background:var(--grey-btn);color:var(--white)}

/* hero */
.hero{top:122px;left:0;width:1200px;height:720px;background:linear-gradient(120deg,#6e6e6e,#a9a9a9 45%,#5c5c5c)}
.hero-title{top:360px;left:0;width:1200px;font-size:74px;font-weight:900;color:var(--white);line-height:1;letter-spacing:1px}
.btn{display:inline-block;background:var(--grey-btn);color:var(--white);font-weight:700;font-size:18px;padding:12px 24px;text-decoration:none}
.hero-btn{top:550px;left:518px}
.dots{top:725px;left:560px;display:flex;gap:10px}
.dots span{width:12px;height:12px;border-radius:50%;background:#333}
.dots span:first-child{background:var(--white)}

h2{font-size:34px;font-weight:900;color:var(--ink);letter-spacing:.5px}
.lead{font-size:14px;line-height:30px;color:var(--text)}

/* services */
.band{left:0;width:1200px;background:var(--band)}
.services-copy{left:75px;top:1468px;width:530px}
.services-copy p{font-size:14px;line-height:30px;margin-top:16px}
.services-photo{left:672px;top:1408px;width:528px;height:460px;background:linear-gradient(135deg,#4f5a68,#a7b0bc 55%,#39424e)}
.services-back{left:650px;top:1440px;width:550px;height:440px;background:#777;transform:rotate(-3deg)}

/* partners */
.card{top:2244px;width:240px;height:310px;background:var(--white);border:1px solid var(--line);border-bottom:3px solid #c9c9c9;text-align:center;padding-top:18px}
.avatar{width:136px;height:136px;border-radius:50%;margin:0 auto;background:linear-gradient(180deg,#c8c8c8,#5e5e5e)}
.card h3{font-size:16px;font-weight:700;color:var(--ink);margin-top:22px}
.card p{font-size:13px;line-height:22px;color:var(--muted);margin-top:6px;padding:0 14px}
.card .outline{display:inline-block;margin-top:10px;border:1.5px solid #555;padding:6px 20px;font-size:13px;font-weight:700;color:var(--ink)}
.arrow{top:2385px}

/* projects */
.filters{top:2870px;left:0;width:1200px;display:flex;justify-content:center;gap:6px}
.filters span{font-size:14px;font-weight:700;color:var(--ink);padding:8px 12px}
.filters span.active{background:#222;color:var(--white);padding:8px 18px}
.tile{width:330px;height:218px}

/* blog */
.post{top:3816px;width:513px;height:368px;background:var(--band);text-align:center;padding:11px}
.post-img{width:100%;height:192px}
.post h3{font-size:16px;font-weight:700;color:var(--ink);margin-top:26px}
.post p{font-size:13px;line-height:26px;color:var(--text);margin-top:4px;padding:0 40px}
.post .link{font-size:13px;font-weight:700;color:var(--ink);margin-top:14px}

/* contact + footer */
.footer{top:4513px;left:0;width:1200px;height:326px;background:var(--dark)}
.contact-box{top:4242px;left:75px;width:1052px;height:359px;background:var(--white);border-radius:8px;box-shadow:0 2px 12px rgba(0,0,0,.15);overflow:hidden}
.contact-side{left:0;top:0;width:408px;height:359px;background:linear-gradient(160deg,#3c3c3c,#6b6b6b 60%,#2e2e2e)}
.contact-side h2{position:absolute;left:40px;top:118px;color:var(--white);font-size:36px}
.contact-side p{position:absolute;left:40px;top:168px;width:340px;color:var(--white);font-size:20px;font-weight:700;line-height:28px}
.field{height:42px;border:1.5px solid #bbb;font-size:13px;color:#555;padding:14px 12px;background:var(--white)}
.submit{left:450px;top:276px;width:166px;height:48px;background:var(--grey-btn);color:var(--white);font-weight:700;font-size:18px;text-align:center;line-height:48px}
.footer-nav{top:4728px;left:0;width:1200px;display:flex;justify-content:center;gap:42px}
.footer-nav a{font-size:14px;color:var(--white);text-decoration:none}
.copyright{top:4768px;left:0;width:1200px;font-size:14px;color:#ddd}
.socials{top:4808px;left:0;width:1200px;display:flex;justify-content:center;gap:22px}
.socials span{width:18px;height:18px;border-radius:50%;background:var(--white)}
</style>
</head>
<body>

<header class="abs site-header">
  <div class="abs brand"><span class="brand-mark"></span><span class="brand-name">Harlow Ridge Financial Partners</span></div>
  <nav class="abs main-nav">
    <a class="active" href="#">HOME</a><a href="#">ABOUT US</a><a href="#">SERVICES</a><a href="#">PROJECTS</a><a href="#">PARTNER</a><a href="#">CONTACT</a>
  </nav>
</header>

<section class="abs hero" role="img" aria-label="Photo of advisers meeting a client at a desk with charts"></section>
<h1 class="abs hero-title center">HARLOW RIDGE<br>FINANCIAL</h1>
<a class="abs btn hero-btn" href="#">READ MORE</a>
<div class="abs dots"><span></span><span></span><span></span><span></span></div>
<svg class="abs" style="top:760px;left:0" width="1200" height="120" viewBox="0 0 1200 120">
  <path d="M0 60 C250 110 420 20 700 50 S1050 90 1200 50 L1200 120 L0 120Z" fill="var(--wave)"/>
  <path d="M0 75 C200 60 380 120 640 85 S1000 55 1200 70 L1200 120 L0 120Z" fill="var(--white)"/>
</svg>

<section>
  <h2 class="abs center" style="top:955px;left:0;width:1200px">WELCOME TO OUR WEBSITE</h2>
  <p class="abs lead center" style="top:1012px;left:100px;width:1000px">Sed iaculis sollicitudin lorem eu volutpat. Donec vehicula lacus eget commodo posuere. Quisque dignissim diam sit amet nulla convallis blandit.<br>Donec erat augue, efficitur a enim sed, eleifend ultricies urna. Cras velit elit, faucibus sed ullamcorper eu, aliquam eget ligula.<br>Maecenas hendrerit commodo orci, ac eleifend felis rutrum sed.</p>
  <a class="abs btn" style="top:1138px;left:518px;font-size:16px" href="#">READ MORE</a>
</section>

<div class="abs band" style="top:1300px;height:700px"></div>
<svg class="abs" style="top:1240px;left:0" width="1200" height="110" viewBox="0 0 1200 110">
  <path d="M0 60 C200 30 330 90 600 40 S1000 0 1200 20 L1200 110 L0 110Z" fill="var(--wave)"/>
  <path d="M0 75 C250 55 420 110 700 70 S1050 40 1200 60 L1200 110 L0 110Z" fill="var(--band)"/>
</svg>
<div class="abs services-back"></div>
<div class="abs services-photo" role="img" aria-label="Photo of business people reviewing a chart on a tablet"></div>
<section class="abs services-copy">
  <h2>OUR SERVICES</h2>
  <p>Sed iaculis sollicitudin lorem eu volutpat. Donec vehicula lacus eget commodo posuere. Quisque dignissim diam sit amet nulla convallis blandit erat augue, efficitur a enim sed, eleifend ultricies urna. Cras velit elit, faucibus sed ullamcorper eu, aliquam eget ligula. Maecenas hendrerit commodo orci, ac eleifend felis rutrum sed.</p>
  <p>Sed placerat tellus ut ex volutpat, vel convallis sapien condimentum. Praesent in eros et lectus sagittis consectetur in vel ante.</p>
  <a class="btn" style="margin-top:22px;font-size:17px;padding:10px 22px" href="#">READ MORE</a>
</section>
<svg class="abs" style="top:1940px;left:0" width="1200" height="90" viewBox="0 0 1200 90">
  <path d="M0 10 C300 50 500 0 800 40 S1100 60 1200 20 L1200 90 L0 90Z" fill="var(--wave)"/>
  <path d="M0 20 C250 70 520 30 820 60 S1100 50 1200 40 L1200 90 L0 90Z" fill="var(--white)"/>
</svg>

<section>
  <h2 class="abs center" style="top:2085px;left:0;width:1200px">PARTNER BIOS</h2>
  <p class="abs lead center" style="top:2145px;left:100px;width:1000px">Sed iaculis sollicitudin lorem eu volutpat. Donec vehicula lacus eget commodo posuere. Quisque dignissim diam sit amet nulla convallis blandit.<br>Donec erat augue, efficitur a enim sed, eleifend ultricies urna.</p>
  <svg class="abs arrow" style="left:42px" width="20" height="32" viewBox="0 0 20 32"><path d="M16 2 L4 16 L16 30" fill="none" stroke="#333" stroke-width="2"/></svg>
  <svg class="abs arrow" style="left:1140px" width="20" height="32" viewBox="0 0 20 32"><path d="M4 2 L16 16 L4 30" fill="none" stroke="#333" stroke-width="2"/></svg>
  <article class="abs card" style="left:75px"><div class="avatar" role="img" aria-label="Partner portrait"></div><h3>NAME HEADING</h3><p>Cras magna ex, euismod id risus sit amet, pretium mollis</p><span class="outline">Read More</span></article>
  <article class="abs card" style="left:345px"><div class="avatar" role="img" aria-label="Partner portrait"></div><h3>NAME HEADING</h3><p>Cras magna ex, euismod id risus sit amet, pretium mollis</p><span class="outline">Read More</span></article>
  <article class="abs card" style="left:617px"><div class="avatar" role="img" aria-label="Partner portrait"></div><h3>NAME HEADING</h3><p>Cras magna ex, euismod id risus sit amet, pretium mollis</p><span class="outline">Read More</span></article>
  <article class="abs card" style="left:886px"><div class="avatar" role="img" aria-label="Partner portrait"></div><h3>NAME HEADING</h3><p>Cras magna ex, euismod id risus sit amet, pretium mollis</p><span class="outline">Read More</span></article>
</section>

<div class="abs band" style="top:2700px;height:880px"></div>
<svg class="abs" style="top:2610px;left:0" width="1200" height="140" viewBox="0 0 1200 140">
  <path d="M0 70 C250 40 420 100 650 40 S1000 20 1200 40 L1200 140 L0 140Z" fill="var(--wave)"/>
  <path d="M0 95 C260 70 450 120 700 90 S1020 70 1200 85 L1200 140 L0 140Z" fill="var(--band)"/>
</svg>
<section>
  <h2 class="abs center" style="top:2800px;left:0;width:1200px">PROJECTS</h2>
  <div class="abs filters"><span class="active">ALL</span><span>PROJECTS COMPLETED</span><span>PROJECTS IN-PROCESS</span></div>
  <div class="abs tile" style="top:2948px;left:75px;background:linear-gradient(135deg,#3e5a7e,#a7b7cc)" role="img" aria-label="Project photo: financial report on a desk"></div>
  <svg class="abs" style="top:3039px;left:220px" width="40" height="40" viewBox="0 0 40 40"><circle cx="20" cy="20" r="20" fill="#222"/><circle cx="18" cy="18" r="6" fill="none" stroke="#fff" stroke-width="2.5"/><path d="M22.5 22.5 L28 28" stroke="#fff" stroke-width="2.5"/></svg>
  <div class="abs tile" style="top:2948px;left:436px;background:linear-gradient(135deg,#d8d8d8,#5a5a5a)" role="img" aria-label="Project photo: partners in a meeting room"></div>
  <div class="abs tile" style="top:2948px;left:796px;background:linear-gradient(135deg,#6a4f7a,#c3b7d2 60%,#8a8fa5)" role="img" aria-label="Project photo: financial growth graphic"></div>
  <div class="abs tile" style="top:3196px;left:75px;background:linear-gradient(135deg,#bfc6cf,#f0f0f0 60%,#8892a0)" role="img" aria-label="Project photo: laptop with charts"></div>
  <div class="abs tile" style="top:3196px;left:436px;background:linear-gradient(135deg,#3e5f86,#9fb2c7)" role="img" aria-label="Project photo: documents and tablet on a desk"></div>
  <div class="abs tile" style="top:3196px;left:796px;background:linear-gradient(135deg,#3b3b3b,#9a9a9a 60%,#dcdcdc)" role="img" aria-label="Project photo: businessman over a city skyline"></div>
</section>
<svg class="abs" style="top:3520px;left:0" width="1200" height="100" viewBox="0 0 1200 100">
  <path d="M0 25 C250 0 450 60 700 30 S1000 10 1200 35 L1200 100 L0 100Z" fill="var(--wave)"/>
  <path d="M0 40 C280 30 470 90 720 60 S1020 40 1200 60 L1200 100 L0 100Z" fill="var(--white)"/>
</svg>

<section>
  <h2 class="abs center" style="top:3685px;left:0;width:1200px">BLOG POSTS</h2>
  <p class="abs lead center" style="top:3742px;left:200px;width:800px">Sed iaculis sollicitudin lorem eu volutpat. Donec vehicula lacus eget commodo posuere. Quisque dignissim diam sit<br>amet nulla convallis blandit.</p>
  <article class="abs post" style="left:75px"><div class="post-img" style="background:linear-gradient(135deg,#2f2f2f,#8a8a8a 60%,#cfcfcf)" role="img" aria-label="Blog photo: traders at computer screens"></div><h3>ETIAM VEL PURUS EGET LIGULA EFFICITUR AUCTOR</h3><p>Phasellus molestie porta erat at vulputate. Curabitur quam leo, bibendum et est ut, euismod dignissim neque.</p><div class="link">READ MORE</div></article>
  <article class="abs post" style="left:614px"><div class="post-img" style="background:linear-gradient(135deg,#4f6f96,#c9d3de)" role="img" aria-label="Blog photo: hand with pen over financial charts"></div><h3>ETIAM VEL PURUS EGET LIGULA EFFICITUR AUCTOR</h3><p>Phasellus molestie porta erat at vulputate. Curabitur quam leo, bibendum et est ut, euismod dignissim neque.</p><div class="link">READ MORE</div></article>
</section>

<footer class="abs footer"></footer>
<section class="abs contact-box">
  <div class="abs contact-side" role="img" aria-label="Photo of office towers">
    <h2>QUICK CONTACT</h2>
    <p>PRAESENT LUCTUS LEO EGET ALIQUAM CONDIMENTUM RUT NEQUE BIBENDUM</p>
  </div>
  <div class="abs field" style="left:451px;top:41px;width:268px">NAME</div>
  <div class="abs field" style="left:735px;top:41px;width:268px">EMAIL ADDRESS</div>
  <div class="abs field" style="left:451px;top:98px;width:268px">PHONE</div>
  <div class="abs field" style="left:735px;top:98px;width:268px">SUBJECT</div>
  <div class="abs field" style="left:451px;top:155px;width:552px;height:100px">MESSAGE</div>
  <div class="abs submit">SUBMIT</div>
</section>
<nav class="abs footer-nav"><a href="#">HOME</a><a href="#">ABOUT US</a><a href="#">SERVICES</a><a href="#">PROJECTS</a><a href="#">PARTNER</a><a href="#">CONTACT</a></nav>
<p class="abs copyright center">Copyright © 2020, Harlow Ridge Financial Partners All Right reserved</p>
<div class="abs socials"><span></span><span></span><span></span><span></span><span></span></div>

</body>
</html>
```